PulseClaimDesk.Com PowerPoint

I need a PowerPoint layout for my presentations. My business is called PulseClaimDesk.Com - my presentations teach cardiologists how to document their procedures and visits and teaches them how to bill accurately for them.

Industry/Entity Type

Business

Requirements
Must have
• the logo should be subtly there on each page - perhaps as a watermark? I'm really not creative; please help.

```html
<!DOCTYPE html>
<html lang="en">
<head>
<meta charset="utf-8">
<title>PulseClaimDesk.Com – Slide Layout</title>
<link rel="stylesheet" href="https://fonts.googleapis.com/css2?family=Graduate&family=Cinzel:wght@400&family=PT+Sans:wght@400&display=swap">
<style>
  :root {
    --page: #ffffff;
    --paper-light: #f2f2f2;
    --paper-mid: #dcdcdc;
    --paper-dark: #cfcfcf;
    --accent-red: #c01f2f;
    --ink: #141414;
    --rule: #333333;
    --band: #1e1e1e;
    --band-text: #ffffff;
    --brand-text: #d9d9d9;
  }
  html, body {
    margin: 0;
    padding: 0;
    width: 1200px;
    height: 900px;
    overflow: hidden;
    background: var(--page);
  }
  .slide-canvas { display: block; width: 1200px; height: 900px; }
  .heading-varsity { font-family: "Graduate", "Georgia", serif; fill: var(--accent-red); }
  .sub-bullet-text { font-family: "Cinzel", "Times New Roman", serif; fill: var(--ink); font-size: 24px; }
  .caption-text { font-family: "PT Sans", "Arial", sans-serif; fill: var(--band-text); font-size: 19px; }
  .page-number { font-family: "PT Sans", "Arial", sans-serif; font-weight: 400; fill: var(--band-text); font-size: 24px; }
  .brand-name { font-family: "PT Sans", "Arial", sans-serif; fill: var(--brand-text); font-size: 15px; }
</style>
</head>
<body>
<svg class="slide-canvas" viewBox="0 0 1200 900" xmlns="http://www.w3.org/2000/svg">
  <defs>
    <radialGradient id="paper-gradient" cx="0.45" cy="0.45" r="0.75">
      <stop offset="0" stop-color="var(--paper-light)"/>
      <stop offset="0.6" stop-color="var(--paper-mid)"/>
      <stop offset="1" stop-color="var(--paper-dark)"/>
    </radialGradient>
  </defs>

  <!-- Slide background -->
  <rect class="slide-background" x="17" y="163" width="1166" height="655" fill="url(#paper-gradient)" role="img" aria-label="Light grey crumpled paper texture background"/>

  <!-- Header rule with marker -->
  <g class="header-rule">
    <line x1="78" y1="211" x2="1082" y2="211" stroke="var(--rule)" stroke-width="4"/>
    <rect x="41" y="195" width="32" height="32" rx="6" transform="rotate(45 57 211)" fill="var(--page)" stroke="var(--rule)" stroke-width="3"/>
    <circle cx="57" cy="211" r="9" fill="var(--accent-red)"/>
  </g>

  <!-- Page number corner -->
  <g class="page-corner">
    <polygon points="1063,177 1167,177 1167,280" fill="var(--accent-red)"/>
    <text class="page-number" x="1144" y="218" text-anchor="middle">03</text>
  </g>

  <!-- Main bullet -->
  <g class="main-bullet">
    <polygon points="139,267 157,267 167,284 157,301 139,301 129,284" fill="none" stroke="var(--accent-red)" stroke-width="5" stroke-linejoin="round"/>
    <text class="heading-varsity" x="188" y="304" font-size="46" textLength="292" lengthAdjust="spacingAndGlyphs">MAIN BULLET</text>
  </g>

  <!-- Sub bullets -->
  <g class="sub-bullets">
    <g class="sub-bullet">
      <polygon points="226,328 242,328 251,343 242,358 226,358 217,343" fill="var(--accent-red)" stroke="var(--ink)" stroke-width="4" stroke-linejoin="round"/>
      <text class="sub-bullet-text" x="262" y="352" textLength="214" lengthAdjust="spacingAndGlyphs">SUB BULLET FORM</text>
    </g>
    <g class="sub-bullet">
      <polygon points="226,386 242,386 251,401 242,416 226,416 217,401" fill="var(--accent-red)" stroke="var(--ink)" stroke-width="4" stroke-linejoin="round"/>
      <text class="sub-bullet-text" x="262" y="410" textLength="214" lengthAdjust="spacingAndGlyphs">SUB BULLET FORM</text>
    </g>
    <g class="sub-bullet">
      <polygon points="226,442 242,442 251,457 242,472 226,472 217,457" fill="var(--accent-red)" stroke="var(--ink)" stroke-width="4" stroke-linejoin="round"/>
      <text class="sub-bullet-text" x="260" y="466" textLength="214" lengthAdjust="spacingAndGlyphs">SUB BULLET FORM</text>
    </g>
  </g>

  <!-- Title band -->
  <g class="title-band">
    <rect x="34" y="661" width="1133" height="146" fill="var(--band)"/>
    <text class="heading-varsity" x="58" y="742" font-size="68" textLength="425" lengthAdjust="spacingAndGlyphs">SLIDE TITLE</text>
    <line x1="58" y1="754" x2="483" y2="754" stroke="var(--band-text)" stroke-width="3"/>
    <text class="caption-text" x="484" y="784" text-anchor="end">BULLET FORM</text>
  </g>

  <!-- Brand mark -->
  <g class="brand-mark">
    <circle cx="1014" cy="783" r="8" fill="var(--accent-red)"/>
    <text class="brand-name" x="1028" y="788">PulseClaimDesk.Com</text>
  </g>
</svg>
</body>
</html>
```